Request for Business Card Design

Hi. My name is Marlene, I am looking for a new business card design for my company, Quarrow Signal Instruments, LLC. I really like the design you did for Tarsel Venture and was hoping you could do something similar using our full logo and our mark. I am also open to any raised texture design using our mark. I have attached our full logo, which would need to be somewhere on the card, as well as the mark in both outline and full form, as well as our brand colors / guide. The card does not have to be white, as long as our logo and mark appear. I actually like darker colored business cards more, but am open to all options. If you are interested in working with me, please let me know. We would also take the business card design into letterhead design if you can do that.

```html
<!DOCTYPE html>
<html lang="en">
<head>
<meta charset="utf-8">
<title>Quarrow Signal Instruments – Business Card</title>
<link href="https://fonts.googleapis.com/css2?family=Montserrat:wght@400;500;700&display=swap" rel="stylesheet">
<style>
  :root {
    --backdrop: #1f1f20;
    --card-dark: #464648;
    --card-light: #ffffff;
    --brand-blue: #1297c4;
    --ink: #2e2e30;
    --ink-soft: #444446;
    --on-dark: #f4f4f4;
  }
  * { box-sizing: border-box; margin: 0; padding: 0; }
  html, body {
    width: 1200px; height: 880px; overflow: hidden;
    background: var(--backdrop);
    font-family: "Montserrat", Arial, sans-serif;
  }
  .canvas {
    position: relative; width: 1200px; height: 880px;
    display: flex; align-items: center; justify-content: center; gap: 40px;
  }
  .card {
    position: relative; width: 540px; height: 309px; overflow: hidden;
    box-shadow: 0 14px 30px rgba(0,0,0,.45);
  }
  .card--front { background: var(--card-dark); display: flex; align-items: center; justify-content: center; }
  .card--back { background: var(--card-light); }

  .brand { display: flex; align-items: center; gap: 14px; }
  .brand__dot { border-radius: 50%; background: var(--brand-blue); flex: none; }
  .brand__name { font-weight: 700; text-transform: uppercase; letter-spacing: .06em; line-height: 1.1; }
  .card--front .brand__dot { width: 62px; height: 62px; }
  .card--front .brand__name { color: var(--on-dark); font-size: 26px; }
  .card--back .brand { position: absolute; top: 30px; right: 30px; gap: 10px; }
  .card--back .brand__dot { width: 34px; height: 34px; }
  .card--back .brand__name { color: var(--ink); font-size: 15px; }

  .holder { position: absolute; left: 34px; top: 112px; }
  .holder__name { font-size: 19px; font-weight: 700; letter-spacing: .02em; color: var(--ink); }
  .holder__first { color: var(--brand-blue); }
  .holder__role { font-size: 13px; color: var(--ink); margin-top: 2px; }

  .address {
    position: absolute; right: 30px; top: 150px; text-align: right;
    font-size: 12px; line-height: 1.45; color: var(--ink);
  }

  .contacts { position: absolute; left: 34px; top: 178px; list-style: none; }
  .contacts li { display: flex; align-items: center; gap: 9px; font-size: 12px; color: var(--ink); height: 20px; }
  .contacts svg { width: 13px; height: 13px; fill: var(--brand-blue); flex: none; }

  .footer-band { position: absolute; left: 0; bottom: 0; width: 540px; height: 309px; }
</style>
</head>
<body>
<main class="canvas">

  <section class="card card--front" aria-label="Card front">
    <div class="brand">
      <span class="brand__dot"></span>
      <span class="brand__name">Quarrow Signal<br>Instruments</span>
    </div>
  </section>

  <section class="card card--back" aria-label="Card back">
    <svg class="footer-band" viewBox="0 0 540 309" preserveAspectRatio="none" aria-hidden="true">
      <polygon points="0,290 398,290 420,242 540,242 540,309 0,309" fill="var(--card-dark)"/>
      <polygon points="0,276 402,276 408,266 412,263 408,272 405,283 0,283" fill="var(--brand-blue)"/>
    </svg>

    <div class="brand">
      <span class="brand__dot"></span>
      <span class="brand__name">Quarrow Signal<br>Instruments</span>
    </div>

    <div class="holder">
      <p class="holder__name"><span class="holder__first">TAVIN</span> HOLLOWAY</p>
      <p class="holder__role">Owner</p>
    </div>

    <p class="address">2840 Lindell Row, Ste<br>210, Fairhaven, TX 75390</p>

    <ul class="contacts">
      <li>
        <svg viewBox="0 0 16 16"><path d="M3 2h3l1 4-2 1a8 8 0 0 0 4 4l1-2 4 1v3a1 1 0 0 1-1 1A12 12 0 0 1 2 3a1 1 0 0 1 1-1z"/></svg>
        555.014.2290
      </li>
      <li>
        <svg viewBox="0 0 16 16"><path d="M1 3h14v10H1z M1 3l7 6 7-6" stroke="#fff" stroke-width="1.2"/></svg>
        info@quarrowsignal.com
      </li>
      <li>
        <svg viewBox="0 0 16 16"><circle cx="8" cy="8" r="7"/><path d="M1 8h14M8 1c-3 4-3 10 0 14M8 1c3 4 3 10 0 14" stroke="#fff" stroke-width="1" fill="none"/></svg>
        www.quarrowsignal.com
      </li>
    </ul>
  </section>

</main>
</body>
</html>
```